need a business card designed, I work with independent car dealerships throughout the US, I connect them with Buyers ( private investors, banks, credit unions, finance co's etc... ) that want to purchase their loan portfolio's, also consult on cashflow management, business lines of credit etc... looking for a consultant look, but something that attracts small business owners
Halvorsen Consulting

```html
<!DOCTYPE html>
<html lang="en">
<head>
<meta charset="utf-8">
<title>Halvorsen Consulting — Business Card</title>
<link rel="stylesheet" href="https://fonts.googleapis.com/css2?family=Open+Sans:wdth,wght@75..100,300..700&family=Tenor+Sans&family=Crimson+Pro:wght@300;400&display=swap">
<style>
  :root {
    --paper: #ffffff;
    --ink: #1c1b1f;
    --card-black: #000000;
    --brand-blue: #00a0dc;
    --tag-blue: #3a9bc9;
    --name-grey: #333333;
    --label-ink: #1a1a1a;
    --white: #ffffff;
  }
  * { margin: 0; padding: 0; box-sizing: border-box; }
  html, body { width: 1200px; height: 1000px; overflow: hidden; background: var(--paper); }
  .sheet { position: relative; width: 1200px; height: 1000px; }

  .card { position: absolute; overflow: hidden; }
  .card--front {
    left: 256px; top: 62px; width: 694px; height: 396px;
    background: var(--paper);
    box-shadow: 0 8px 18px rgba(0,0,0,0.28);
  }
  .card__shapes { position: absolute; inset: 0; }

  .brand { position: absolute; display: flex; align-items: center; }
  .brand--front { left: 88px; top: 40px; }
  .brand__square { width: 44px; height: 44px; background: var(--brand-blue); margin-right: 24px; }
  .brand__name {
    font-family: "Tenor Sans", sans-serif;
    font-size: 35px; letter-spacing: 0.5px; color: var(--brand-blue);
    text-transform: uppercase; white-space: nowrap;
  }

  .holder {
    position: absolute; left: 100px; top: 108px;
    font-family: "Open Sans", sans-serif; font-stretch: 80%;
    font-weight: 300; font-size: 30px; color: var(--name-grey);
  }

  .tagline {
    position: absolute; left: 408px; top: 196px;
    font-family: "Open Sans", sans-serif; font-stretch: 92%;
    font-size: 19px; line-height: 28px; color: var(--tag-blue);
  }

  .contacts { position: absolute; left: 380px; top: 278px; list-style: none; }
  .contacts__item {
    display: flex; align-items: center; height: 33px;
    font-family: "Open Sans", sans-serif; font-stretch: 92%;
    font-size: 20px; color: var(--white);
  }
  .contacts__item--mobile { font-weight: 700; }
  .contacts__icon { width: 20px; height: 20px; margin-right: 8px; }

  .card--back {
    top: 601px; width: 454px; height: 259px; background: var(--card-black);
    text-align: center;
  }
  .card--lower { left: 78px; }
  .card--upper { left: 658px; }
  .back__brand {
    position: absolute; left: 0; right: 0; top: 78px;
    font-family: "Tenor Sans", sans-serif; font-size: 16px; letter-spacing: 2px;
    color: var(--white); text-transform: uppercase;
  }
  .back__url {
    position: absolute; left: 0; right: 0; top: 122px;
    font-family: "Crimson Pro", serif; color: var(--brand-blue);
  }
  .card--lower .back__url { font-size: 27px; }
  .card--upper .back__url { font-size: 21px; text-transform: uppercase; letter-spacing: 0.6px; top: 128px; }

  .label {
    position: absolute; top: 892px;
    font-family: "Crimson Pro", serif; font-weight: 300; font-size: 50px; color: var(--label-ink);
  }
  .label--lower { left: 193px; }
  .label--or { left: 579px; }
  .label--upper { left: 781px; }
</style>
</head>
<body>
<main class="sheet">

  <section class="card card--front" aria-label="Card front">
    <svg class="card__shapes" viewBox="0 0 694 396" width="694" height="396" aria-hidden="true">
      <polygon points="694,150 396,150 196,396 184,396 388,150" fill="none"/>
      <polygon points="694,152 392,152 192,396 210,396 402,160 694,160" fill="var(--brand-blue)"/>
      <polygon points="694,160 402,160 210,396 694,396" fill="var(--ink)"/>
    </svg>

    <div class="brand brand--front">
      <span class="brand__square"></span>
      <span class="brand__name">Halvorsen Consulting</span>
    </div>

    <p class="holder">Marcus T Halvorsen</p>

    <p class="tagline">Excellent Service<br>and Expedited Funding</p>

    <ul class="contacts">
      <li class="contacts__item contacts__item--mobile">
        <svg class="contacts__icon" viewBox="0 0 20 20" aria-hidden="true">
          <rect x="6" y="3" width="8" height="14" rx="1.5" fill="var(--brand-blue)"/>
          <rect x="7.5" y="5" width="5" height="4" fill="var(--white)"/>
        </svg>
        303 555 0148
      </li>
      <li class="contacts__item">
        <svg class="contacts__icon" viewBox="0 0 20 20" aria-hidden="true">
          <rect x="2" y="5" width="16" height="12" rx="1.5" fill="var(--brand-blue)"/>
          <rect x="5" y="2" width="8" height="5" fill="var(--white)"/>
          <rect x="5" y="9" width="10" height="5" fill="var(--white)" opacity="0.6"/>
        </svg>
        303 555 0192
      </li>
      <li class="contacts__item">
        <svg class="contacts__icon" viewBox="0 0 20 20" aria-hidden="true">
          <rect x="3" y="5" width="14" height="10" fill="var(--white)"/>
          <polyline points="3,5 10,11 17,5" fill="none" stroke="var(--brand-blue)" stroke-width="1.4"/>
        </svg>
        dealdesk7@mailbox.net
      </li>
    </ul>
  </section>

  <section class="card card--back card--lower" aria-label="Card back, lowercase web address">
    <p class="back__brand">Halvorsen Consulting</p>
    <p class="back__url">www.halvorsenconsulting.net</p>
  </section>

  <section class="card card--back card--upper" aria-label="Card back, uppercase web address">
    <p class="back__brand">Halvorsen Consulting</p>
    <p class="back__url">www.halvorsenconsulting.net</p>
  </section>

  <p class="label label--lower">lowercase</p>
  <p class="label label--or">or</p>
  <p class="label label--upper">uppercase</p>

</main>
</body>
</html>
```